The Plate Compass

Cutting Through the Noise to What Actually Works.

Nutrition book

Target Market(s)

People looking to be or get healthy and eat right.

```html
<!DOCTYPE html>
<html lang="en">
<head>
<meta charset="UTF-8">
<title>The Plate Compass</title>
<link rel="stylesheet" href="https://fonts.googleapis.com/css2?family=Anton&family=Oswald:wght@500;600&family=Roboto+Condensed:wght@400;700&family=Montserrat:wght@700;800&display=swap">
<style>
  :root {
    --paper: #f7f5ee;
    --forest: #1f4a22;
    --olive: #5f8a2a;
    --ink: #1d2a33;
    --body: #3a3a36;
    --rule: #a9b98a;
    --band: #57802a;
    --band-text: #f3f0e4;
  }
  * { margin: 0; padding: 0; box-sizing: border-box; }
  html, body { width: 800px; height: 1200px; overflow: hidden; background: var(--paper); }
  .cover { position: relative; width: 800px; height: 1200px; background: var(--paper); }

  .title-kicker {
    position: absolute; top: 60px; left: 0; width: 800px;
    display: flex; align-items: center; justify-content: center; gap: 28px;
    font-family: "Anton", sans-serif; font-size: 64px; color: var(--forest); letter-spacing: 4px;
  }
  .title-kicker .rule { width: 230px; height: 3px; background: var(--olive); }

  .title-main {
    position: absolute; top: 140px; left: 0; width: 800px; text-align: center;
    font-family: "Anton", sans-serif; font-size: 220px; line-height: 1; color: var(--forest);
    letter-spacing: 6px;
  }
  .title-sub {
    position: absolute; top: 380px; left: 0; width: 800px; text-align: center;
    font-family: "Oswald", sans-serif; font-weight: 600; font-size: 112px; line-height: 1;
    color: var(--olive); letter-spacing: 14px;
  }

  .pyramid {
    position: absolute; left: 215px; top: 505px; width: 530px; height: 570px;
    clip-path: polygon(50% 0, 100% 100%, 0 100%);
    background: linear-gradient(180deg, #c9a24a 0%, #b5704a 28%, #c9a067 50%, #7fa04a 70%, #3f7a34 100%);
  }

  .pillars { position: absolute; left: 40px; top: 550px; width: 200px; list-style: none; }
  .pillar { display: flex; gap: 14px; height: 136px; padding-top: 14px; border-bottom: 1.5px solid var(--rule); }
  .pillar:last-child { border-bottom: none; }
  .pillar-icon { flex: none; width: 50px; height: 50px; border: 2px solid var(--olive); border-radius: 50%;
    display: flex; align-items: center; justify-content: center; }
  .pillar-icon svg { width: 26px; height: 26px; }
  .pillar-name { font-family: "Roboto Condensed", sans-serif; font-weight: 700; font-size: 19px; color: var(--forest); margin-bottom: 4px; }
  .pillar-text { font-family: "Roboto Condensed", sans-serif; font-size: 16px; line-height: 1.25; color: var(--body); }

  .stamp {
    position: absolute; left: 572px; top: 510px; width: 190px; height: 190px; border-radius: 50%;
    border: 3px solid var(--olive); display: flex; align-items: center; justify-content: center;
  }
  .stamp::before { content: ""; position: absolute; inset: 6px; border-radius: 50%; border: 1.5px solid var(--olive); }
  .stamp-text { text-align: center; font-family: "Montserrat", sans-serif; font-weight: 800; font-size: 17px; line-height: 1.2; letter-spacing: 1px; }
  .stamp-text .dark { color: var(--ink); }
  .stamp-text .green { color: var(--olive); }
  .stamp-text .to { display: flex; align-items: center; justify-content: center; gap: 8px; color: var(--ink); }
  .stamp-text .to::before, .stamp-text .to::after { content: ""; width: 16px; height: 2px; background: var(--ink); }

  .band {
    position: absolute; left: 0; bottom: 0; width: 800px; height: 100px; background: var(--band);
    display: flex; align-items: center; justify-content: center; gap: 22px;
    font-family: "Oswald", sans-serif; font-weight: 500; font-size: 23px; letter-spacing: 3px; color: var(--band-text);
  }
  .band svg { width: 18px; height: 18px; }
</style>
</head>
<body>
<main class="cover">
  <div class="title-kicker"><span class="rule"></span>THE<span class="rule"></span></div>
  <h1 class="title-main">PLATE</h1>
  <div class="title-sub">COMPASS</div>

  <div class="pyramid" role="img" aria-label="Food pyramid built from tiers of real food: oils, nuts and berries at the top, then fish, chicken and eggs, then grains, avocado and sweet potato, and a wide base of vegetables and fruit"></div>

  <ul class="pillars">
    <li class="pillar">
      <span class="pillar-icon"><svg viewBox="0 0 24 24" fill="none" stroke="#5f8a2a" stroke-width="1.8"><path d="M7 3h10v6a5 5 0 0 1-10 0z"/><path d="M7 5H4v2a3 3 0 0 0 3 3M17 5h3v2a3 3 0 0 1-3 3M12 14v4M8 21h8M9 18h6"/></svg></span>
      <div><div class="pillar-name">RESULTS</div><div class="pillar-text">Sustainable habits. Real life. Real results.</div></div>
    </li>
    <li class="pillar">
      <span class="pillar-icon"><svg viewBox="0 0 24 24" fill="none" stroke="#5f8a2a" stroke-width="1.8"><path d="M9 3h6M10 3v6L4.5 19a1.5 1.5 0 0 0 1.3 2h12.4a1.5 1.5 0 0 0 1.3-2L14 9V3M7 15h10"/></svg></span>
      <div><div class="pillar-name">STRATEGY</div><div class="pillar-text">Supplements and timing can support your goals.</div></div>
    </li>
    <li class="pillar">
      <span class="pillar-icon"><svg viewBox="0 0 24 24" fill="none" stroke="#5f8a2a" stroke-width="1.8"><path d="M7 3v18M4 3v5a3 3 0 0 0 6 0V3M17 21V3c-2 1-3 4-3 7h3"/></svg></span>
      <div><div class="pillar-name">FOUNDATION</div><div class="pillar-text">Macros matter. Balance drives progress.</div></div>
    </li>
    <li class="pillar">
      <span class="pillar-icon"><svg viewBox="0 0 24 24" fill="none" stroke="#5f8a2a" stroke-width="1.8"><path d="M5 19C5 10 11 5 20 4c0 9-5 15-13 15zM5 19l8-8"/></svg></span>
      <div><div class="pillar-name">BASE</div><div class="pillar-text">Whole foods. Consistent choices. Every day.</div></div>
    </li>
  </ul>

  <div class="stamp">
    <p class="stamp-text">
      <span class="dark">CUTTING</span><br>
      <span class="dark">THROUGH</span><br>
      <span class="dark">THE NOISE</span><br>
      <span class="to">TO</span>
      <span class="green">WHAT</span><br>
      <span class="green">ACTUALLY</span><br>
      <span class="green">WORKS.</span>
    </p>
  </div>

  <footer class="band">
    <span>EAT WELL. LIVE WELL.</span>
    <svg viewBox="0 0 24 24" fill="none" stroke="#f3f0e4" stroke-width="2"><path d="M5 19C5 10 11 5 20 4c0 9-5 15-13 15zM5 19l8-8"/></svg>
    <span>BUILD A HEALTHY LIFE THAT LASTS.</span>
  </footer>
</main>
</body>
</html>
```